Book Title: “Faith: Road of Endless Grace” Please see the attachment “Text on the cover”.

Book Cover Design Instructions: This book is meant for people of all religions and nationalities. Therefore, on the cover, there should be no mosque or an object specific to any religion. The primary emphasis should be on the "unconditional love of God." Therefore, use universal symbols of love. The second priority themes could be Sufism, Peace, and self-improvement. Rest is your imagination. Please also see the attachment: 'Book description and author's Bio.'
This book has the potential to be a best seller. Please do a good job.
What Book Cover Formats are required: A designer should submit cover designs in three formats: (1) eBook, (2) Paperback, and (3) Hardback. These books will be published on Borvex QPL.
Format requirements for eBooks are available from: https://qpl.borvex.example/en_US/help/topic/R731928457.
You can find paperback and hardback cover measurements from: https://qpl.borvex.example/en_US/cover-calculator
• To complete the project, all three formats should be accepted by Borvex QPL.
• The book interior trim size is 6.14 X 9.21 inches.
• Interior Type: Premium color.
• No bleed.
• I do not upload barcode. So, the back cover should have room for Borvex to print the barcode.
• Number of pages 126.
Compensation for the designer: After selecting one designer, I will increase the amount by $200 on Artvelle to compensate for three deliverables.
Follow-up of the Project:
After the book is published, I may need minor revisions. For example, the number of pages may change. Therefore, I will need the same design in revised sizes. In that case, I will pay $25 for each revision. For example, if the number of pages changes, I will need a different spine for paperback and hardback, then I will pay the artist $25 + $25 = $50 for both designs.
List of Enclosers:
1. Text on the cover.
2. Book description and author's Bio for the back cover.
3. Later, I will upload my picture for the book's back cover.

Target Market(s)

Any adult

Industry/Entity Type

Any industry

Requirements
Must have
• Three Deliverables

```html
<!DOCTYPE html>
<html lang="en">
<head>
<meta charset="utf-8">
<title>Faith: Road of Endless Grace — Full Cover</title>
<link href="https://fonts.googleapis.com/css2?family=Cinzel:wght@400;600;700&family=Montserrat:wght@400;500&display=swap" rel="stylesheet">
<style>
  :root {
    --page: #ffffff;
    --cover-blue: #3f628d;
    --text-light: #ffffff;
    --subtitle-blue: #3a5688;
    --sky-top: #4f72a8;
    --sky-mid: #9fb4d8;
    --glow: #fff6d2;
    --cloud-warm: #f3d7b8;
    --cloud-rose: #d7bfd8;
    --placeholder: #ffffff;
    --barcode-edge: #c88a3a;
  }
  * { box-sizing: border-box; margin: 0; padding: 0; }
  html, body {
    width: 1200px; height: 1200px; overflow: hidden;
    background: var(--page);
  }
  .canvas { position: relative; width: 1200px; height: 1200px; }
  .cover {
    position: absolute; left: 50px; top: 205px;
    width: 1101px; height: 791px;
    background: var(--cover-blue);
    box-shadow: 0 1px 3px rgba(0,0,0,.25);
  }
  /* Back cover */
  .back { position: absolute; left: 0; top: 0; width: 522px; height: 100%; color: var(--text-light); }
  .back-title {
    position: absolute; left: 33px; top: 36px; width: 478px;
    font-family: 'Cinzel', serif; font-weight: 400; font-size: 25.5px;
    letter-spacing: 1.2px; white-space: nowrap;
  }
  .back-subtitle {
    position: absolute; left: 34px; top: 78px;
    font-family: 'Cinzel', serif; font-weight: 400; font-size: 13.6px;
    letter-spacing: .6px; white-space: nowrap;
  }
  .blurb {
    position: absolute; left: 33px; top: 98px; width: 462px;
    font-family: 'Montserrat', sans-serif; font-size: 10.4px; line-height: 12.7px;
    text-align: justify;
  }
  .blurb p + p { margin-top: 12.7px; }
  .author-photo {
    position: absolute; left: 33px; top: 546px; width: 134px; height: 168px;
    background: var(--placeholder);
  }
  .bio-name {
    position: absolute; left: 183px; top: 543px;
    font-family: 'Cinzel', serif; font-size: 20px; letter-spacing: 1px; white-space: nowrap;
  }
  .bio {
    position: absolute; left: 183px; top: 572px; width: 312px;
    font-family: 'Montserrat', sans-serif; font-size: 10.4px; line-height: 12.7px;
    text-align: justify;
  }
  .barcode-area {
    position: absolute; left: 306px; top: 657px; width: 192px; height: 104px;
    background: var(--placeholder); border: 1px solid var(--barcode-edge);
  }
  /* Spine */
  .spine { position: absolute; left: 522px; top: 0; width: 48px; height: 100%; color: var(--text-light); }
  .spine-text {
    position: absolute; left: 50%; writing-mode: vertical-rl;
    transform: translateX(-50%);
    font-family: 'Cinzel', serif; font-size: 23px; letter-spacing: 1px; white-space: nowrap;
  }
  .spine-title { top: 40px; }
  .spine-author { top: 537px; }
  /* Front cover */
  .front { position: absolute; left: 570px; top: 0; width: 531px; height: 100%; }
  .front-art {
    position: absolute; left: 0; top: 0; width: 531px; height: 716px;
    background:
      radial-gradient(circle at 52% 46%, var(--glow) 0%, #fde9a6 10%, rgba(250,222,160,.75) 24%, rgba(243,215,184,0) 46%),
      radial-gradient(ellipse at 20% 85%, var(--cloud-rose) 0%, rgba(215,191,216,0) 45%),
      radial-gradient(ellipse at 85% 80%, var(--cloud-rose) 0%, rgba(215,191,216,0) 45%),
      radial-gradient(ellipse at 50% 95%, var(--cloud-warm) 0%, rgba(243,215,184,0) 55%),
      linear-gradient(180deg, var(--sky-top) 0%, #6f8fc0 30%, var(--sky-mid) 60%, #c9bdd8 100%);
  }
  .front-title {
    position: absolute; left: 0; top: 30px; width: 531px; text-align: center;
    font-family: 'Cinzel', serif; font-weight: 400; color: var(--text-light);
    text-shadow: 0 1px 0 #6c7ea6, 0 2px 4px rgba(30,50,90,.45);
    line-height: 1;
  }
  .front-title span { display: block; }
  .title-line-1 { font-size: 94px; }
  .title-line-2 { font-size: 70px; margin-top: 6px; }
  .title-line-3 { font-size: 52px; margin-top: 4px; }
  .front-subtitle {
    position: absolute; left: 0; top: 472px; width: 531px; text-align: center;
    font-family: 'Cinzel', serif; font-weight: 700; font-style: italic;
    font-size: 25px; line-height: 32px; color: var(--subtitle-blue);
    text-shadow: 0 1px 2px rgba(255,255,255,.6);
  }
  .front-author {
    position: absolute; left: 0; top: 738px; width: 531px; text-align: center;
    font-family: 'Cinzel', serif; font-size: 27px; letter-spacing: 1.5px;
    color: var(--text-light);
  }
</style>
</head>
<body>
<div class="canvas">
  <div class="cover">
    <section class="back">
      <h2 class="back-title">FAITH: ROAD OF ENDLESS GRACE</h2>
      <h3 class="back-subtitle">GUIDE TO CULTIVATING INNER PEACE AND MINDFUL LIVING</h3>
      <div class="blurb">
        <p>This book intricately intertwines the diverse teachings of Sufism with the deep wisdom of the Quran to create a comprehensive roadmap for personal spiritual growth. The reader has a chance to experience firsthand the profound peace and boundless love Sufis have cherished for centuries. This book addresses the following critical questions:</p>
        <p>How can one unconditionally love God? It is the greatest of all kinds of love that ignites a profound and transformative spiritual journey.</p>
        <p>How to feel the love of God, which can bring immense peace and contentment.</p>
        <p>How to unconditionally love yourself, which nurtures personal growth and harmony.</p>
        <p>What is the most effective way to respond to life’s critical crises to reduce suffering and expedite recovery?</p>
        <p>This book also explores Islam’s overwhelming emphasis on avoiding Zulm (oppression and injustice) because the Quran mentions the word Zulm an astounding 291 times. Avoiding Zulm in all human interactions should be the top priority for every Muslim.</p>
        <p>Prophet Muhammad (PBUH) did not just preach peace and love. He gave us a practical example when he took over as a ruler of the Medina without bloodshed. He did not inherit power through the dynasty, and Medina was multi-religious. Arguably, it was history’s first large-scale peaceful transfer of power.</p>
        <p>Similarly, he signed the Treaty of Hudaybia with the staunchest enemy, employing an unprecedented peaceful strategy to nonviolently end a bitter war that had claimed hundreds of lives.</p>
        <p>The highlight of this book is that it points to the methodology to acquire a fully satisfied and contented soul (Nafs-e-Mutma’inna) in practical steps, which is the goal of every Sufi wayfarer.</p>
      </div>
      <div class="author-photo" role="img" aria-label="Space reserved for the author's portrait"></div>
      <h3 class="bio-name">DR. IDRIS HARLAN</h3>
      <p class="bio">Dr. Harlan holds a Master’s in Physics and a Master’s in Computer Science and worked as a Software Engineer. He earned his Ph.D. in Islamic Studies. He was one of the founders of a mosque in Virginia.</p>
      <div class="barcode-area" aria-label="Space reserved for printer barcode"></div>
    </section>

    <section class="spine">
      <span class="spine-text spine-title">FAITH: ROAD OF ENDLESS GRACE</span>
      <span class="spine-text spine-author">DR. IDRIS HARLAN</span>
    </section>

    <section class="front">
      <div class="front-art" role="img" aria-label="Illustration of a radiant sun bursting through a starry sky framed by soft pastel clouds"></div>
      <h1 class="front-title">
        <span class="title-line-1">FAITH</span>
        <span class="title-line-2">ROAD OF</span>
        <span class="title-line-3">ENDLESS GRACE</span>
      </h1>
      <p class="front-subtitle">Guide to Cultivating Inner<br>Peace and Mindful Living</p>
      <p class="front-author">DR. IDRIS HARLAN</p>
    </section>
  </div>
</div>
</body>
</html>
```